Business Cards - Brightpath Horizon

need to design unique business card for my mortgage business. I need to design credit card style business card for my business or any unique idea that you might have

Target Market(s)

Home Loan customers

Industry/Entity Type

Mortgage Brokerage

Contact Information for Business Card

please design credit card style or very unique style business card

Colors

Designer to choose colors to be used in the design.

Requirements
Must have
• Name
• position
• Phone number
• fax number
• email address
• website address
• social media address
• All above fields will be provided once design in finalised

```html
<!DOCTYPE html>
<html lang="en">
<head>
<meta charset="utf-8">
<title>Brightpath Horizon – Business Card</title>
<link rel="stylesheet" href="https://fonts.googleapis.com/css2?family=Libre+Baskerville:wght@400&family=Share+Tech+Mono&display=swap">
<style>
  :root {
    --page-bg: #d9d4cc;
    --card-deep: #0b2f9e;
    --card-mid: #1a4fd0;
    --card-light: #3f7ee6;
    --band: rgba(255, 255, 255, 0.07);
    --band-dark: rgba(0, 20, 90, 0.22);
    --ink-light: #f2f4fa;
    --ink-soft: #c9d3ea;
    --ink-gold: #e7c9a0;
    --accent-orange: #f07a1c;
    --foliage: rgba(180, 205, 245, 0.28);
  }
  * { margin: 0; padding: 0; box-sizing: border-box; }
  html, body {
    width: 1200px;
    height: 969px;
    overflow: hidden;
    background: var(--page-bg);
  }
  .canvas {
    position: relative;
    width: 1200px;
    height: 969px;
  }
  .card {
    position: absolute;
    left: 100px;
    top: 200px;
    width: 1000px;
    height: 570px;
    border-radius: 30px;
    overflow: hidden;
    background: linear-gradient(100deg, var(--card-deep) 0%, var(--card-mid) 45%, var(--card-light) 100%);
    box-shadow: 0 18px 40px rgba(0, 0, 0, 0.25);
    font-family: "Libre Baskerville", Georgia, serif;
  }
  .card-bands {
    position: absolute;
    inset: 0;
    width: 100%;
    height: 100%;
  }
  .foliage {
    position: absolute;
    right: 0;
    top: 40px;
    width: 480px;
    height: 470px;
    background: radial-gradient(ellipse at 60% 40%, var(--foliage) 0%, rgba(180, 205, 245, 0.12) 45%, rgba(180, 205, 245, 0) 72%);
  }
  .brand {
    position: absolute;
    left: 64px;
    top: 110px;
    display: flex;
    align-items: center;
    gap: 14px;
    color: var(--ink-light);
    font-size: 34px;
    letter-spacing: 1px;
  }
  .brand-mark {
    width: 22px;
    height: 22px;
    background: var(--accent-orange);
  }
  .social {
    position: absolute;
    right: 54px;
    top: 122px;
    display: flex;
    gap: 10px;
  }
  .social-dot {
    width: 40px;
    height: 40px;
    border-radius: 50%;
    background: rgba(240, 244, 252, 0.85);
  }
  .card-number {
    position: absolute;
    left: 220px;
    top: 262px;
    font-family: "Share Tech Mono", monospace;
    font-size: 70px;
    letter-spacing: 6px;
    color: var(--ink-light);
    text-shadow: 0 2px 2px rgba(0, 0, 0, 0.25);
    word-spacing: 18px;
  }
  .holder {
    position: absolute;
    right: 52px;
    top: 378px;
    text-align: right;
  }
  .holder-name {
    font-size: 30px;
    color: var(--ink-gold);
    letter-spacing: 0.5px;
  }
  .holder-title {
    margin-top: 6px;
    font-size: 22px;
    color: var(--ink-soft);
  }
  .contact {
    position: absolute;
    right: 52px;
    top: 460px;
    text-align: right;
    font-size: 19px;
    color: var(--ink-soft);
    line-height: 36px;
  }
  .contact-label { color: var(--ink-gold); }
</style>
</head>
<body>
<div class="canvas">
  <div class="card">
    <svg class="card-bands" viewBox="0 0 1000 570" preserveAspectRatio="none" aria-hidden="true">
      <polygon points="0,40 60,0 420,0 0,300" fill="var(--band)"/>
      <polygon points="0,420 380,170 560,420 380,570 0,570" fill="var(--band-dark)"/>
      <polygon points="380,170 700,0 1000,0 1000,120 560,420" fill="var(--band)"/>
      <rect x="0" y="220" width="60" height="50" fill="var(--band)"/>
      <rect x="0" y="290" width="60" height="50" fill="var(--band)"/>
    </svg>
    <div class="foliage" role="img" aria-label="Faint tree foliage decoration"></div>

    <div class="brand"><span class="brand-mark"></span>Brightpath Horizon</div>

    <div class="social" aria-label="Social media">
      <span class="social-dot"></span>
      <span class="social-dot"></span>
      <span class="social-dot"></span>
      <span class="social-dot"></span>
    </div>

    <div class="card-number">315 704 2268</div>

    <div class="holder">
      <div class="holder-name">DANIEL REYES</div>
      <div class="holder-title">CEO/FOUNDER</div>
    </div>

    <div class="contact">
      <div>2190 Willow Crest Road, Juneau, Alaska 99801</div>
      <div><span class="contact-label">P:</span> 555 218 4096 &nbsp;<span class="contact-label">E:</span> hello@brightpathhome.com &nbsp;<span class="contact-label">W:</span> www.brightpathhome.com</div>
    </div>
  </div>
</div>
</body>
</html>
```